Elevating our current Business Card Design

We want to elevate our current business card with a new design to look like a zenith 300 company. We are a premium lubricant distributor (oil and grease).
We need 2 versions, version 1 is as per the uploaded a copy of our current business card with the English version.
For our Chinese version we need to use the front to be English in English and have the back of the card designed exactly like the front for all info to be in Chinese.
The design template needs to be such that we can amend the template with adding different information for each person's card.
The background colour of the card can be changed- we just need to clearly see all information on the card and logos.
The QJR and Ember steady logos cannot have any colour or display changes- only use the logos attached.
All logos need to be included and all information from the attached current card

```html
<!DOCTYPE html>
<html lang="en">
<head>
<meta charset="utf-8">
<title>Meridian Lube Partners – Business Card</title>
<link rel="stylesheet" href="https://fonts.googleapis.com/css2?family=Open+Sans:wght@400;600;700&display=swap">
<style>
  :root {
    --backdrop: #232323;
    --card: #28272b;
    --red: #ee2c24;
    --red-deep: #8e1418;
    --gold: #eab32b;
    --white: #ffffff;
    --badge: #f26f21;
    --badge-ring: #8a8a8c;
  }
  * { box-sizing: border-box; margin: 0; padding: 0; }
  html, body { width: 1200px; height: 780px; overflow: hidden; }
  body {
    background: var(--backdrop);
    font-family: "Open Sans", Arial, sans-serif;
    color: var(--white);
    position: relative;
  }
  .card {
    position: absolute;
    width: 540px;
    height: 309px;
    background: var(--card);
    border-radius: 18px;
    overflow: hidden;
    box-shadow: 0 14px 30px rgba(0,0,0,.55);
  }
  .card--front { left: 40px; top: 235px; }
  .card--back  { left: 620px; top: 235px; }

  /* front */
  .front-brand {
    position: absolute; inset: 0;
    display: flex; align-items: center; justify-content: center; gap: 18px;
  }
  .front-brand__dot {
    width: 46px; height: 46px; border-radius: 50%; background: var(--gold);
  }
  .front-brand__name {
    font-size: 58px; font-weight: 700; color: var(--red); letter-spacing: 1px;
  }

  /* back */
  .swoosh { position: absolute; left: 0; top: 0; width: 540px; height: 309px; }
  .holder {
    position: absolute; right: 34px; top: 26px; text-align: right;
    transform: rotate(-8deg); transform-origin: right top;
  }
  .holder__name { font-size: 24px; font-weight: 600; line-height: 1.1; }
  .holder__title { font-size: 12.5px; font-weight: 400; letter-spacing: .3px; }

  .contact {
    position: absolute; left: 38px; top: 178px; font-size: 12px; line-height: 1.45;
  }
  .contact__address { margin-bottom: 8px; padding-left: 22px; }
  .contact__list { list-style: none; }
  .contact__item { display: flex; align-items: center; gap: 8px; }
  .contact__icon { width: 13px; height: 13px; flex: none; }

  .badges {
    position: absolute; right: 30px; top: 172px; display: flex; gap: 16px;
  }
  .badge {
    width: 38px; height: 38px; border-radius: 50%; background: var(--badge);
    border: 4px solid var(--badge-ring);
  }
  .partners {
    position: absolute; right: 30px; bottom: 28px; display: flex; height: 46px;
  }
  .partners__distributor {
    border: 2px solid var(--red); border-right: none;
    display: flex; align-items: center; padding: 0 12px;
    font-size: 12px; font-weight: 700; color: var(--red);
  }
  .partners__supplier {
    background: var(--red); display: flex; align-items: center; padding: 0 16px;
    font-size: 16px; font-weight: 700; color: var(--white); letter-spacing: .5px;
  }
</style>
</head>
<body>

<section class="card card--front" aria-label="Card front">
  <div class="front-brand">
    <span class="front-brand__dot"></span>
    <span class="front-brand__name">MERIDIAN</span>
  </div>
</section>

<section class="card card--back" aria-label="Card back">
  <svg class="swoosh" viewBox="0 0 540 309" aria-hidden="true">
    <defs>
      <linearGradient id="band" x1="0" y1="0" x2="1" y2="0">
        <stop offset="0" stop-color="var(--red)"/>
        <stop offset=".45" stop-color="var(--red)"/>
        <stop offset="1" stop-color="var(--red-deep)"/>
      </linearGradient>
      <linearGradient id="goldline" x1="0" y1="0" x2="1" y2="0">
        <stop offset="0" stop-color="#f4c22f"/>
        <stop offset="1" stop-color="#c8901e"/>
      </linearGradient>
    </defs>
    <path d="M0 0 H540 V58 C470 120 330 140 150 150 C80 155 30 160 0 170 Z" fill="url(#band)"/>
    <path d="M540 62 C470 132 330 150 150 160 C80 164 30 170 0 182" fill="none" stroke="url(#goldline)" stroke-width="5"/>
  </svg>

  <div class="holder">
    <p class="holder__name">Marla Keswick</p>
    <p class="holder__title">Administration Executive</p>
  </div>

  <div class="contact">
    <p class="contact__address">48 Freight Way<br>Dunmore, WA 6199</p>
    <ul class="contact__list">
      <li class="contact__item">
        <svg class="contact__icon" viewBox="0 0 16 16"><path d="M3 1 L6 4 L4.5 6 C5.5 8.5 7.5 10.5 10 11.5 L12 10 L15 13 L13 15 C6.5 14.5 1.5 9.5 1 3 Z" fill="var(--red)"/></svg>
        1300 472 615
      </li>
      <li class="contact__item">
        <svg class="contact__icon" viewBox="0 0 16 16"><rect x="4" y="1" width="8" height="14" rx="1.5" fill="none" stroke="var(--red)" stroke-width="1.6"/></svg>
        +61 455 019 734
      </li>
      <li class="contact__item">
        <svg class="contact__icon" viewBox="0 0 16 16"><rect x="1" y="6" width="14" height="9" rx="1" fill="var(--red)"/><rect x="4" y="1" width="8" height="6" fill="none" stroke="var(--red)" stroke-width="1.5"/></svg>
        +61 8 9520 4461
      </li>
      <li class="contact__item">
        <svg class="contact__icon" viewBox="0 0 16 16"><circle cx="8" cy="8" r="6.5" fill="none" stroke="var(--red)" stroke-width="1.6"/><path d="M1.5 8 H14.5 M8 1.5 C5 5 5 11 8 14.5 C11 11 11 5 8 1.5" fill="none" stroke="var(--red)" stroke-width="1.2"/></svg>
        www.meridianlube.com
      </li>
      <li class="contact__item">
        <svg class="contact__icon" viewBox="0 0 16 16"><rect x="1" y="3" width="14" height="10" rx="1" fill="var(--red)"/><path d="M1.5 4 L8 9 L14.5 4" fill="none" stroke="var(--card)" stroke-width="1.4"/></svg>
        marla.k@meridianlube.com
      </li>
    </ul>
  </div>

  <div class="badges" aria-label="Certification badges">
    <span class="badge"></span>
    <span class="badge"></span>
    <span class="badge"></span>
  </div>

  <div class="partners">
    <div class="partners__distributor">Meridian Lube Partners</div>
    <div class="partners__supplier">ORVANE</div>
  </div>
</section>

</body>
</html>
```